I want ideas sample designs for my book cover

Hello,

We need a book cover designed in flat and 3D Versions. We would like to have jpg and png for final output and include a copy of the PSD for future revisions.

Here are the basic details:

Title: The Harvest of Quiet Builders
Author: Norman Quillfeather

Dimensions of book:

Was looking at the Pavo website for dimensions. I thought you may want to go on there and look at the different sizes. I used the 6x9” perfect bound US trade size for my book. You will see that this has a spine width of 0.225”, Cover size of 12.48 x 9.25” and spine begins at 6.125”

If you need background info on the author just to get an idea what he does, please check:

http://NormanQuillfeather.example

IMPORTANT: Please see attached document for a more detailed info:

Exact Title Of book
Back Cover
Spine Info
Measurements of book and dimension
Examples of book covers
Norman's photo attached

Thanks,
Darlene

Industry/Entity Type

Life Coaching

Font styles to use
Serif

Requirements
Must have
• Jpg, png and PSD files
• title
• author
• exact dimensions
• front and back cover
• flat and 3d versions

```html
<!DOCTYPE html>
<html lang="en">
<head>
<meta charset="utf-8">
<title>The Harvest of Quiet Builders — Cover Wrap</title>
<link href="https://fonts.googleapis.com/css2?family=Anton&family=Arimo:wght@700&family=Oswald:wght@300;400&family=Source+Sans+3:ital,wght@0,400;1,400&display=swap" rel="stylesheet">
<style>
  :root {
    --orange: #f07a22;
    --panel-top: rgba(238, 140, 80, 0.86);
    --panel-bottom: rgba(150, 72, 30, 0.88);
    --ink: #111111;
    --white: #ffffff;
    --sky-blue: #9cc4dc;
    --sky-warm: #f2c48a;
    --sea-deep: #1f4f8c;
    --sea-mid: #3a78b8;
    --jacket: #14161c;
  }
  * { margin: 0; padding: 0; box-sizing: border-box; }
  html, body { width: 1200px; height: 893px; overflow: hidden; background: #fff; }
  .cover {
    position: relative;
    width: 1200px;
    height: 893px;
    overflow: hidden;
    font-family: "Source Sans 3", sans-serif;
  }
  .cover-photo {
    position: absolute; inset: 0;
    background:
      linear-gradient(90deg, transparent 0 46%, rgba(20,22,28,0.0) 47%, rgba(20,22,28,0.92) 56%, rgba(20,22,28,0.92) 66%, rgba(20,22,28,0.55) 76%, transparent 86%),
      linear-gradient(180deg, var(--sky-blue) 0%, #d9d4c0 22%, var(--sky-warm) 40%, #d6d3c8 48%, var(--sea-mid) 55%, var(--sea-deep) 72%, #5e90c6 86%, var(--sea-deep) 100%);
  }
  .back-panel {
    position: absolute;
    left: 22px; top: 14px;
    width: 544px; height: 874px;
    background: linear-gradient(180deg, var(--panel-top) 0%, var(--panel-top) 62%, rgba(210, 110, 60, 0.85) 75%, var(--panel-bottom) 100%);
  }
  .back-copy {
    position: absolute;
    left: 38px; top: 50px;
    width: 513px;
    color: var(--ink);
    font-size: 12.6px;
    line-height: 17.6px;
    text-align: justify;
  }
  .back-copy p + p { margin-top: 17.6px; }
  .author-photo {
    position: absolute;
    left: 35px; top: 642px;
    width: 157px; height: 160px;
    background: linear-gradient(160deg, #f4f4f4, #b9b9b9);
  }
  .author-bio {
    position: absolute;
    left: 218px; top: 648px;
    width: 333px;
    color: var(--white);
    font-size: 10.6px;
    line-height: 14.3px;
    text-align: justify;
  }
  .author-site {
    position: absolute;
    left: 61px; top: 826px;
    color: var(--white);
    font-size: 11.5px;
    font-style: italic;
  }
  .isbn-box {
    position: absolute;
    left: 326px; top: 803px;
    width: 148px; height: 72px;
    background: var(--white);
    font-size: 8px;
    text-align: center;
    padding-top: 10px;
    color: var(--ink);
  }
  .spine-title {
    position: absolute;
    left: 588px; top: 240px;
    writing-mode: vertical-rl;
    color: var(--orange);
    font-size: 13px;
    letter-spacing: 2.4px;
    text-transform: uppercase;
  }
  .spine-photo {
    position: absolute;
    left: 589px; top: 656px;
    width: 21px; height: 29px;
    background: linear-gradient(160deg, #f1f1f1, #a9a9a9);
  }
  .spine-author {
    position: absolute;
    left: 590px; top: 780px;
    writing-mode: vertical-rl;
    color: var(--white);
    font-size: 14px;
  }
  .front-kicker {
    position: absolute;
    right: 40px; top: 276px;
    font-family: "Oswald", sans-serif;
    font-weight: 300;
    font-size: 22px;
    color: var(--ink);
    transform: scaleX(0.86);
    transform-origin: right;
  }
  .front-author {
    position: absolute;
    right: 38px; top: 302px;
    font-family: "Arimo", sans-serif;
    font-weight: 700;
    font-size: 47px;
    color: var(--ink);
    letter-spacing: 0.5px;
  }
  .front-title {
    position: absolute;
    left: 640px; top: 400px;
    width: 530px; height: 210px;
  }
  .front-title text { font-family: "Anton", sans-serif; fill: var(--orange); }
  .front-subtitle {
    position: absolute;
    left: 644px; top: 650px;
    width: 290px;
    color: var(--white);
    font-size: 23px;
    line-height: 32.2px;
  }
</style>
</head>
<body>
<main class="cover">
  <div class="cover-photo" role="img" aria-label="Photograph of a man in a dark jacket gazing out over a bright ocean at sunset, spanning the whole wrap"></div>

  <section class="back-panel">
    <div class="back-copy">
      <p>This path goes way beyond Entrepreneurism! This is a book for the awakening Entrepreneurs who are building businesses for a better world, affecting generations to come. Bringing you disruptive (in a good way) information, to turn you and your business inside-out for maximum acceleration towards your organisational vision, mission and values.</p>
      <p>There is the potential to have a more meaningful life and business by discovering the symbiotic relationship that exists between all beings. You will be empowered to take your life and business to the next level if you answer the call in this book. It will introduce you to the power of Amazonian plant medicine and other entheogens for improving relationships with yourself, your partner and your family, friends, business associates and Mother Earth.</p>
      <p>An entheogen is defined as ‘a substance (usually from a plant, but not always) that is consumed in order to alter one’s state of consciousness or to act as a catalyst towards encounters with other states of being.’ Plant medicine has been successfully used in South America for thousands of years. This ancient wisdom is helping billionaires, industry icons and entrepreneurs to be better leaders, awakening to its potential for allowing deep examination of the psyche which has the ability to heal, eliminate fears and create a new level of success both personally and professionally.</p>
      <p>Norman shares his own heart-felt personal experiences and insights gained from working with these substances and the amazing medicine men and women of the Amazon who retain thousands of years of ancient wisdom. He has spent years turning himself inside-out to powerfully transform his own life and business and wants to encourage entrepreneurs to do the same. He believes that if enough people have the opportunity to explore their own consciousness, then together we can make a positive impact on humanity. If you are ready to travel to the fringes and take a journey within, you will discover that you are the missing link you have been looking for. Get ready to expand your consciousness, transform your business and create a new inspiring lifestyle, which will benefit all beings and our beautiful Mother Earth.</p>
    </div>
    <div class="author-photo" role="img" aria-label="Black and white portrait photo of the author"></div>
    <p class="author-bio">Norman Quillfeather is an internationally-renowned entrepreneur, speaker, philanthropist, thought leader and best-selling author. Having played the role of transformational coach, facilitator and spoken to over three million people from twelve different countries, he challenges you in his second book to journey deep within yourself to examine the core of your true nature and how it impacts your entrepreneurial journey. Some of the world biggest game changers, social entrepreneurs, internet marketers and consultants have reported that Norman’s golden edge is to integrate “purpose with profits” in a way that brings greater meaning to the work they are doing here in the world.</p>
    <p class="author-site">www.NormanQuillfeather.example</p>
    <div class="isbn-box">ISBN</div>
  </section>

  <p class="spine-title">The Harvest of Quiet Builders</p>
  <div class="spine-photo" role="img" aria-label="Small author portrait on spine"></div>
  <p class="spine-author">Norman Quillfeather</p>

  <p class="front-kicker">From the Best Selling Author of “Unfold”</p>
  <h2 class="front-author">Norman Quillfeather</h2>
  <svg class="front-title" viewBox="0 0 530 210" aria-label="The Harvest of Quiet Builders">
    <defs>
      <filter id="title-shadow" x="-5%" y="-5%" width="115%" height="120%">
        <feDropShadow dx="2" dy="3" stdDeviation="1.5" flood-color="#000" flood-opacity="0.45"/>
      </filter>
    </defs>
    <text x="38" y="92" font-size="40" transform="rotate(-90 38 92)" textLength="72" lengthAdjust="spacingAndGlyphs" filter="url(#title-shadow)">The</text>
    <text x="56" y="96" font-size="100" textLength="468" lengthAdjust="spacingAndGlyphs" filter="url(#title-shadow)">HARVEST OF QUIET</text>
    <text x="4" y="204" font-size="100" textLength="520" lengthAdjust="spacingAndGlyphs" filter="url(#title-shadow)">BUILDERS</text>
  </svg>
  <p class="front-subtitle">How this ancient wisdom is helping billionaires, industry icons and entrepreneurs to be better leaders, increase impact and leave a legacy</p>
</main>
</body>
</html>
```